IT Company needs Website for new Web and Mobile products for Sports and Fitness

Background:

We developed web based white label frontend web solution, backend services and white label mobile apps for to log, analyze, share and control sport and fitness activities. The name of this product suite is "Trevantix" (http://trevantix-example.com)

This products will be used by customers that provide platforms and community systems for sport and fitness. One of the major USP's is, that our technology i open for nearly all common formats, devices and apps out in the market. This means, you can just upload your data directly from device, file or app - e.G. Kestrel, Bolvane, Ravelo, StrideVault, Pacelumo, Zembra and much others.

Two current concrete examples/References

(1) MyQuorel
It's an international platform from quorel for runners. It provides individual training lans and a training log. MyQuorel uses the Backend Product "Trevantix Hub" (see http://hub.trevantix-example.net for a landing page) to integrate device, file and app support. Before this, every user has to track his training with manual inputs

(2) Paceharbor and fen-zine
Both are German customers. Paceharor is focused on runners. fen-zine is focused on Triatheletes. Both use the Product "Trevantix Web". This is a complete web solution with web based frontend solutions for athletes and coaches.

What do we need?
We need website layout for B2B for our products. We don't need lot's of pages. We need the pretty and nice layout, so we can derive the pages we need.

IMPORTANT
We don't talk about the webpages for the product itself (this will be a different project in future). We talk about a website, explaining the products)
Updates

Hi all,

we just start reviewing the first designs, and try to give feedback as detailed as possible. We attached a PDF document, to describe the the products a little bit more detailed. 

As written in the description, in the end we have two different sections. One is the usual stuff like "start page", "about", "contact", "disclaimer", "pricing", "blah...." and one will be the Developer Section, the "Tec Section". This ist aimed to developers (of our customers) that will integrate our products in there existing system or which will integrate our services in there own software.  This "pages" are more like "documentation", so easy to read and cool to look at (cause developers likes it cool, but straight)

Dear all,

we just do the final review. Cause this week is with heavy load, it takes some time...

Cheers

Odell

Target Market(s)

* Platforms and Communities for sport, health and fitness
* Gyms

Industry/Entity Type

Concrete

Font styles to use
Sans Serif

Requirements
Must have
• * Templates shall base on bootstrap. If not, it shall be easily realized on our site with bootstrap or out of the box "full responsive"

* HTML5 / CSS3
Nice to have
• PAGES
- Start Page
- Generic Template (from which we can derive additional pages)
- Contact Page
- Disclaimer Page
- Blog/News Page
- "About us" Page (can be combined with disclaimer)
- One Example product page (in end we have 3 products), shall show (if you need product details, let me know)
- product and it's description
- pricing information
- Add-Ons for the product
- Developer Section Page (Start Point for developers, where the finde "basic technical concepts and developer API's
- Example Developer Page for technical concept
- Example Developer Page for API

LOGO ISSUE
You can use an align to the Logo attached OR provide a new logo. The given logo is a logo for our own B2C Website http://trevantix-example.net. It's not really necessary, that the logo or the color must be used for the product website. Maybe it will be better if it's a complete new one, to avoid irritation between Trevantix as a B2B product and trevantix-example.net as a B2C platform.
Should not have
• No Flash and other proprietary technologies

```html
<!DOCTYPE html>
<html lang="en">
<head>
<meta charset="utf-8">
<title>Trevantix – API</title>
<link href="https://fonts.googleapis.com/css2?family=PT+Sans:wght@400;700&family=PT+Sans+Narrow:wght@700&display=swap" rel="stylesheet">
<style>
:root{
  --ink:#3c3c3c;
  --nav:#555;
  --title:#233247;
  --accent:#e8771e;
  --link:#c8140e;
  --frame:#d6d6d6;
  --rule:#e6e6e6;
  --footer:#2b2b2b;
  --footer-text:#d8d8d8;
  --chart-a:#2e5f8a;
  --chart-b:#7fb0d6;
  --chart-c:#e8771e;
  --chart-d:#9aa4ad;
  --chart-fill:#e3edf6;
}
*{box-sizing:border-box;margin:0;padding:0}
html,body{width:1022px;height:1200px;overflow:hidden;background:#fff}
body{position:relative;font-family:"PT Sans",sans-serif;color:var(--ink)}
.site-header{position:absolute;left:0;top:0;width:1022px;height:83px;border-bottom:1px solid var(--rule)}
.brand{position:absolute;left:154px;top:14px}
.brand-name{display:flex;align-items:center;gap:6px;font-weight:700;font-size:26px;color:var(--accent);line-height:1}
.brand-mark{width:14px;height:14px;background:var(--accent)}
.brand-tag{margin-top:12px;font-size:7px;font-weight:700;color:#222}
.main-nav{position:absolute;left:350px;top:30px;display:flex}
.main-nav a{font-size:9px;color:var(--nav);text-decoration:none;padding:0 26px;line-height:20px;border-left:1px solid var(--rule)}
.main-nav a:first-child{border-left:0}
.page-title{position:absolute;left:181px;top:104px;font-family:"PT Sans Narrow",sans-serif;font-weight:700;font-size:19px;color:var(--title)}
.title-shade{position:absolute;left:176px;top:140px;width:380px;height:8px;background:radial-gradient(ellipse at center,#eee 0%,rgba(255,255,255,0) 70%)}
.content-panel{position:absolute;left:160px;top:174px;width:712px;height:927px;border:1px solid var(--frame);border-radius:4px;box-shadow:inset 0 0 10px #ececec}
.entry{position:absolute;left:33px;width:660px;height:150px}
.entry-media{position:absolute;left:0;top:0;width:196px;height:145px;border:2px solid var(--frame);background:#fff;overflow:hidden}
.entry-media svg{display:block}
.entry-body{position:absolute;left:209px;top:4px;width:450px;font-size:9.1px;line-height:13.1px}
.entry-body p{margin-bottom:13px}
.more-link{display:block;margin-left:6px;color:var(--link);text-decoration:none;font-size:9px}
.app-shot{width:100%;height:100%;background:linear-gradient(180deg,#2f79b8 0 8%,#f2f4f6 8% 92%,#1e4f7a 92%)}
.chart-label{font-family:"PT Sans",sans-serif}
.site-footer{position:absolute;left:0;top:1142px;width:1022px;height:58px;background:var(--footer);border-top:3px solid #bbb}
.social{position:absolute;left:178px;top:16px;display:flex;gap:9px}
.social span{width:19px;height:19px;border-radius:2px}
.copyright{position:absolute;right:194px;top:13px;text-align:right;font-size:9.5px;line-height:17px;color:var(--footer-text)}
</style>
</head>
<body>
<header class="site-header">
  <div class="brand">
    <div class="brand-name"><span class="brand-mark"></span>Trevantix</div>
    <div class="brand-tag">DIGITAL SPORT AND FITNESS SERVICES</div>
  </div>
  <nav class="main-nav">
    <a href="#">HOME</a><a href="#">TREVANTIX</a><a href="#">FITNESS CLOUD</a><a href="#">REFERENCES</a><a href="#">PRODUCTS</a><a href="#">SERVICES</a>
  </nav>
</header>

<h1 class="page-title">API</h1>
<div class="title-shade"></div>

<main class="content-panel">
  <article class="entry" style="top:36px">
    <div class="entry-media">
      <svg width="192" height="141" viewBox="0 0 192 141" class="chart-label">
        <text x="96" y="12" font-size="5.5" font-weight="700" text-anchor="middle" fill="#333">API Calls per Endpoint</text>
        <g stroke="#e4e4e4" stroke-width=".5">
          <line x1="14" y1="30" x2="184" y2="30"/><line x1="14" y1="55" x2="184" y2="55"/><line x1="14" y1="80" x2="184" y2="80"/><line x1="14" y1="105" x2="184" y2="105"/>
        </g>
        <line x1="14" y1="126" x2="184" y2="126" stroke="#999" stroke-width=".6"/>
        <g fill="var(--chart-a)">
          <rect x="20" y="60" width="10" height="66"/><rect x="38" y="38" width="10" height="88"/><rect x="56" y="74" width="10" height="52"/><rect x="74" y="50" width="10" height="76"/><rect x="92" y="88" width="10" height="38"/><rect x="110" y="66" width="10" height="60"/><rect x="128" y="96" width="10" height="30"/><rect x="146" y="80" width="10" height="46"/><rect x="164" y="104" width="10" height="22"/>
        </g>
      </svg>
    </div>
    <div class="entry-body">
      <p>Sed ut perspiciatis unde omnis iste natus error sit voluptatem accusantium doloremque laudantium, totam rem aperiam, eaque ipsa quae ab illo inventore veritatis et quasi architecto beatae vitae dicta sunt explicabo. ccusantium doloremque laudantium, totam rem aperiam, eaque ipsa quae ab illo inventore veritatis et quasi architecto beatae vitae dicta sunt explicabo.</p>
      <p>Sed ut perspiciatis unde omnis iste natus error sit voluptatem accusantium doloremque laudantium, totam rem aperiam, eaque ipsa quae ab illo inventore veritatis et quasi architecto beatae vitae dicta sunt explicabo. Sed ut perspiciatis unde omnis iste natus error sit voluptatem</p>
      <a class="more-link" href="#">More&nbsp; Reading &gt;&gt;</a>
    </div>
  </article>

  <article class="entry" style="top:205px">
    <div class="entry-media"><div class="app-shot" role="img" aria-label="Mobile app screenshot showing an exercise library list"></div></div>
    <div class="entry-body">
      <p>Sed ut perspiciatis unde omnis iste natus error sit voluptatem accusantium doloremque laudantium, totam rem aperiam, eaque ipsa quae ab illo inventore veritatis et quasi architecto beatae vitae dicta sunt explicabo. ccusantium doloremque laudantium, totam rem aperiam, eaque ipsa quae ab illo inventore veritatis et quasi architecto beatae vitae dicta sunt explicabo.</p>
      <p>Sed ut perspiciatis unde omnis iste natus error sit voluptatem accusantium doloremque laudantium, totam rem aperiam, eaque ipsa quae ab illo inventore veritatis et quasi architecto beatae vitae dicta sunt explicabo. Sed ut perspiciatis unde omnis iste natus error sit voluptatem</p>
      <a class="more-link" href="#">More&nbsp; Reading &gt;&gt;</a>
    </div>
  </article>

  <article class="entry" style="top:374px">
    <div class="entry-media">
      <svg width="192" height="141" viewBox="0 0 192 141" class="chart-label">
        <text x="96" y="12" font-size="5.5" font-weight="700" text-anchor="middle" fill="#333">Weekly Active Athletes</text>
        <polygon fill="var(--chart-fill)" points="12,100 12,86 36,80 60,70 84,74 108,58 132,50 156,40 180,30 180,100"/>
        <polyline fill="none" stroke="var(--chart-a)" stroke-width="1.2" points="12,86 36,80 60,70 84,74 108,58 132,50 156,40 180,30"/>
        <g fill="var(--chart-a)"><circle cx="12" cy="86" r="1.6"/><circle cx="36" cy="80" r="1.6"/><circle cx="60" cy="70" r="1.6"/><circle cx="84" cy="74" r="1.6"/><circle cx="108" cy="58" r="1.6"/><circle cx="132" cy="50" r="1.6"/><circle cx="156" cy="40" r="1.6"/><circle cx="180" cy="30" r="1.6"/></g>
        <line x1="12" y1="100" x2="180" y2="100" stroke="#999" stroke-width=".6"/>
        <g font-size="4.5" fill="#666" text-anchor="middle"><text x="12" y="108">W1</text><text x="60" y="108">W3</text><text x="108" y="108">W5</text><text x="156" y="108">W7</text></g>
        <g fill="var(--chart-b)"><rect x="10" y="124" width="4" height="8"/><rect x="34" y="120" width="4" height="12"/><rect x="58" y="122" width="4" height="10"/><rect x="82" y="118" width="4" height="14"/><rect x="106" y="121" width="4" height="11"/><rect x="130" y="116" width="4" height="16"/><rect x="154" y="119" width="4" height="13"/><rect x="178" y="114" width="4" height="18"/></g>
      </svg>
    </div>
    <div class="entry-body">
      <p>Sed ut perspiciatis unde omnis iste natus error sit voluptatem accusantium doloremque laudantium, totam rem aperiam, eaque ipsa quae ab illo inventore veritatis et quasi architecto beatae vitae dicta sunt explicabo. ccusantium doloremque laudantium, totam rem aperiam, eaque ipsa quae ab illo inventore veritatis et quasi architecto beatae vitae dicta sunt explicabo.</p>
      <p>Sed ut perspiciatis unde omnis iste natus error sit voluptatem accusantium doloremque laudantium, totam rem aperiam, eaque ipsa quae ab illo inventore veritatis et quasi architecto beatae vitae dicta sunt explicabo. Sed ut perspiciatis unde omnis iste natus error sit voluptatem</p>
      <a class="more-link" href="#">More&nbsp; Reading &gt;&gt;</a>
    </div>
  </article>

  <article class="entry" style="top:557px">
    <div class="entry-media">
      <svg width="192" height="141" viewBox="0 0 192 141" class="chart-label">
        <text x="96" y="12" font-size="5.5" font-weight="700" text-anchor="middle" fill="#333">Sync Response Time</text>
        <g stroke="#e4e4e4" stroke-width=".5"><line x1="12" y1="35" x2="182" y2="35"/><line x1="12" y1="65" x2="182" y2="65"/><line x1="12" y1="95" x2="182" y2="95"/></g>
        <polyline fill="none" stroke="var(--chart-c)" stroke-width="1.2" points="12,70 32,60 52,66 72,48 92,56 112,40 132,52 152,36 172,44 182,38"/>
        <polyline fill="none" stroke="var(--chart-a)" stroke-width="1.2" points="12,100 32,94 52,98 72,86 92,90 112,80 132,84 152,74 172,78 182,72"/>
        <line x1="12" y1="112" x2="182" y2="112" stroke="#999" stroke-width=".6"/>
        <g font-size="4.5" fill="#555"><rect x="40" y="124" width="4" height="4" fill="var(--chart-c)"/><text x="47" y="128">Upload</text><rect x="100" y="124" width="4" height="4" fill="var(--chart-a)"/><text x="107" y="128">Download</text></g>
      </svg>
    </div>
    <div class="entry-body">
      <p>Sed ut perspiciatis unde omnis iste natus error sit voluptatem accusantium doloremque laudantium, totam rem aperiam, eaque ipsa quae ab illo inventore veritatis et quasi architecto beatae vitae dicta sunt explicabo. ccusantium doloremque laudantium, totam rem aperiam, eaque ipsa quae ab illo inventore veritatis et quasi architecto beatae vitae dicta sunt explicabo.</p>
      <p>Sed ut perspiciatis unde omnis iste natus error sit voluptatem accusantium doloremque laudantium, totam rem aperiam, eaque ipsa quae ab illo inventore veritatis et quasi architecto beatae vitae dicta sunt explicabo. Sed ut perspiciatis unde omnis iste natus error sit voluptatem</p>
      <a class="more-link" href="#">More&nbsp; Reading &gt;&gt;</a>
    </div>
  </article>

  <article class="entry" style="top:740px">
    <div class="entry-media">
      <svg width="192" height="141" viewBox="0 0 192 141" class="chart-label">
        <text x="96" y="12" font-size="5.5" font-weight="700" text-anchor="middle" fill="#333">Upload Sources</text>
        <g transform="rotate(-90 70 76)" fill="none" stroke-width="46">
          <circle cx="70" cy="76" r="23" stroke="var(--chart-a)" stroke-dasharray="50.6 144.5"/>
          <circle cx="70" cy="76" r="23" stroke="var(--chart-b)" stroke-dasharray="0 50.6 43.4 144.5"/>
          <circle cx="70" cy="76" r="23" stroke="var(--chart-c)" stroke-dasharray="0 94 31.8 144.5"/>
          <circle cx="70" cy="76" r="23" stroke="var(--chart-d)" stroke-dasharray="0 125.8 18.7 144.5"/>
        </g>
        <g font-size="4.8" fill="#444">
          <rect x="140" y="56" width="4" height="4" fill="var(--chart-a)"/><text x="147" y="60">Device</text>
          <rect x="140" y="68" width="4" height="4" fill="var(--chart-b)"/><text x="147" y="72">File</text>
          <rect x="140" y="80" width="4" height="4" fill="var(--chart-c)"/><text x="147" y="84">App</text>
          <rect x="140" y="92" width="4" height="4" fill="var(--chart-d)"/><text x="147" y="96">Manual</text>
        </g>
      </svg>
    </div>
    <div class="entry-body">
      <p>Sed ut perspiciatis unde omnis iste natus error sit voluptatem accusantium doloremque laudantium, totam rem aperiam, eaque ipsa quae ab illo inventore veritatis et quasi architecto beatae vitae dicta sunt explicabo. ccusantium doloremque laudantium, totam rem aperiam, eaque ipsa quae ab illo inventore veritatis et quasi architecto beatae vitae dicta sunt explicabo.</p>
      <p>Sed ut perspiciatis unde omnis iste natus error sit voluptatem accusantium doloremque laudantium, totam rem aperiam, eaque ipsa quae ab illo inventore veritatis et quasi architecto beatae vitae dicta sunt explicabo. Sed ut perspiciatis unde omnis iste natus error sit voluptatem</p>
      <a class="more-link" href="#">More&nbsp; Reading &gt;&gt;</a>
    </div>
  </article>
</main>

<footer class="site-footer">
  <div class="social">
    <span style="background:#3b5998"></span><span style="background:#3fa9e0"></span><span style="background:#e5e5e5"></span><span style="background:#f29423"></span><span style="background:#c4302b"></span><span style="background:#7f9db2"></span>
  </div>
  <div class="copyright">© 2013 trevantix-example.com, All rights reserved<br>X2</div>
</footer>
</body>
</html>
```